Musical download and streaming website

hello designers, I want to start up a musical website where users can download and rate music of different genres such as RnB, Hip hop, rock, afro-pop. This website should be attractive and contemporary. There will be a search column for different songs. Music files will be mp3, mwa, and others. I like blue, gold, pink and indigo colors. My website should resemble http://tunovalt.com. There should be good imaginary of music stars on my website.

```html
<!DOCTYPE html>
<html lang="en">
<head>
<meta charset="utf-8">
<title>Solenne Music</title>
<link href="https://fonts.googleapis.com/css2?family=Open+Sans:wght@400;600&family=Roboto+Condensed:wght@400;700&display=swap" rel="stylesheet">
<style>
:root{
  --blue:#1e9be0;
  --pink:#e5157a;
  --dark:#222;
  --text:#444;
  --muted:#888;
  --page:#efe7dd;
  --panel:#fff;
  --line:#dcdcdc;
  --star:#f0a30a;
  --download:#e8501e;
}
*{box-sizing:border-box;margin:0;padding:0}
html,body{width:745px;height:1200px;overflow:hidden}
body{background:var(--page);font-family:"Open Sans",sans-serif;color:var(--text);position:relative}
.abs{position:absolute}

.topbar{left:0;top:0;width:745px;height:20px;background:var(--blue);color:#fff;font-size:8px}
.topbar .signin{left:434px;top:5px}
.topbar .mail{left:500px;top:5px}
.topbar .soc{top:4px;width:12px;height:12px;border-radius:50%;background:#fff}

.header{left:0;top:20px;width:745px;height:53px;background:#fff;border-bottom:1px solid #e4ddd4}
.brand{left:61px;top:20px;font-family:"Roboto Condensed",sans-serif;font-size:20px;font-weight:400;color:var(--blue);letter-spacing:.3px}
.nav{top:23px;font-family:"Roboto Condensed",sans-serif;font-size:9px;color:#333;letter-spacing:.3px}
.nav.active{color:var(--blue)}

.panel{left:61px;top:87px;width:623px;height:1005px;background:var(--panel);border:1px solid #e2d9cd}
.hero{left:62px;top:88px;width:621px;height:268px;background:linear-gradient(100deg,#4d6b2c 0%,#8fae46 30%,#c7cd8e 55%,#6d8a3e 80%,#2f4a1e 100%)}
.hero h1{position:absolute;left:64px;top:99px;font-family:"Roboto Condensed",sans-serif;font-weight:700;font-size:29px;color:#fff}
.hero p{position:absolute;left:64px;top:132px;width:230px;font-family:"Roboto Condensed",sans-serif;font-size:11px;line-height:13.5px;color:#fff}
.hero svg{position:absolute;top:0}

.searchband{left:62px;top:356px;width:621px;height:57px;background:var(--pink)}
.radio{top:24px;font-family:"Roboto Condensed",sans-serif;font-size:10.5px;color:#fff;display:flex;align-items:center;gap:3px}
.radio i{width:8px;height:8px;border:1px solid #fff;border-radius:50%;display:block}
.search-input{left:188px;top:18px;width:323px;height:24px;background:#fff;font-size:7px;color:#555;padding:8px 0 0 18px}
.search-btn{left:511px;top:18px;width:69px;height:24px;background:#111;border:1px solid #fff;color:#fff;font-family:"Roboto Condensed",sans-serif;font-size:10px;text-align:center;line-height:22px}

.results-title{left:76px;top:437px;font-family:"Roboto Condensed",sans-serif;font-size:16px;color:#222}
.card{left:77px;width:418px;height:130px;border:1px solid var(--line);background:#fff}
.card .top{position:absolute;left:0;top:0;width:416px;height:68px;background:linear-gradient(#fff,#eee)}
.play{position:absolute;left:9px;top:8px;width:33px;height:33px;border-radius:50%;background:#222}
.play svg{position:absolute;left:12px;top:9px}
.card .title{position:absolute;left:58px;top:9px;font-size:10px;color:#333}
.card .artist{position:absolute;left:58px;top:29px;font-size:7.5px;color:#333}
.card .stars{color:var(--star);font-size:8px;margin-left:6px;letter-spacing:-.5px}
.wave{position:absolute;left:9px;top:50px;width:386px;height:8px;background:repeating-linear-gradient(90deg,#999 0 1px,#ddd 1px 2px)}
.meta{position:absolute;left:11px;top:82px;font-size:6.8px;color:#444;white-space:nowrap}
.meta b{color:var(--blue);font-weight:400}
.meta span{margin-right:7px}
.dl{position:absolute;left:11px;top:99px;width:74px;height:19px;border:1px solid #ccc;border-radius:2px;background:linear-gradient(#fff,#eee);font-size:8px;color:#333;padding:4px 0 0 7px}
.dl i{position:absolute;right:7px;top:4px;width:9px;height:9px;border-radius:50%;background:var(--download)}

.pager{top:1051px;height:15px;border:1px solid #ddd;background:#f6f6f6;font-size:7.5px;font-weight:600;color:#333;text-align:center;line-height:13px}

.ad{left:511px;top:437px;width:156px;height:132px;background:linear-gradient(120deg,#cfd3d6,#7f8a92 60%,#2f3a44);border:1px solid #ccc}
.ad .label{position:absolute;left:6px;top:7px;font-family:"Roboto Condensed",sans-serif;font-size:7px;font-weight:700;color:#ff5500}
.ad .head{position:absolute;left:6px;top:22px;font-family:"Roboto Condensed",sans-serif;font-size:16px;font-weight:700;line-height:17px;color:#fff}
.ad .btn{position:absolute;left:6px;top:85px;width:20px;height:20px;border-radius:50%;background:#ff4a1a}

.albums-head{left:511px;top:579px;width:156px;height:31px;background:var(--pink);color:#fff;font-family:"Roboto Condensed",sans-serif;font-size:12px;padding:9px 0 0 28px}
.albums-head svg{position:absolute;left:10px;top:9px}
.albums{left:511px;top:610px;width:156px;height:188px;background:#222}
.albums .ctrl{position:absolute;top:10px;width:11px;height:11px;border:1px solid #555;border-radius:50%}
.albums .bar{position:absolute;left:66px;top:14px;width:64px;height:3px;background:#666}
.albums ul{list-style:none;position:absolute;left:0;top:38px;width:156px}
.albums li{height:25.5px;font-size:8px;color:#999;padding-left:35px;position:relative;white-space:nowrap;overflow:hidden}
.albums li::before{content:"";position:absolute;left:10px;top:3px;width:6px;height:6px;border:1px solid #444;border-radius:50%}
.promo{left:511px;top:810px;width:156px;height:126px;background:linear-gradient(#5fb6c4,#a6d2d4 55%,#8a6b4d 80%,#5b4533);border:1px solid #ccc}

.shadow{left:150px;top:1092px;width:445px;height:28px}
.fsoc{top:1130px;width:18px;height:18px;border-radius:50%}
.flinks{left:0;top:1161px;width:745px;text-align:center;font-size:7px;color:#333;word-spacing:1px}
.copy{left:0;top:1177px;width:745px;text-align:center;font-size:7px;color:#333}
</style>
</head>
<body>

<div class="abs topbar">
  <span class="abs signin">&#128274; SIGN IN</span>
  <span class="abs mail">&#9993; info@solennemusic.com</span>
  <span class="abs soc" style="left:625px"></span>
  <span class="abs soc" style="left:640px"></span>
  <span class="abs soc" style="left:655px"></span>
  <span class="abs soc" style="left:670px"></span>
</div>

<header class="abs header">
  <div class="abs brand">SOLENNE MUSIC</div>
  <span class="abs nav active" style="left:383px">HOME</span>
  <span class="abs nav" style="left:429px">ABOUT US</span>
  <span class="abs nav" style="left:491px">ALBUM</span>
  <span class="abs nav" style="left:541px">MUSIC</span>
  <span class="abs nav" style="left:589px">EVENTS</span>
  <span class="abs nav" style="left:641px">CONTACTS</span>
</header>

<div class="abs panel"></div>

<section class="abs hero" role="img" aria-label="Smiling woman jogging outdoors with earphones in a sunny green park">
  <h1>SOLENNE MUSIC</h1>
  <p>It is a musical website where users can download and rate music of different genres such as RnB, Hip hop, rock, afro-pop</p>
  <svg style="left:15px" width="20" height="40" viewBox="0 0 20 40"><polyline points="18,2 2,20 18,38" fill="none" stroke="#fff" stroke-width="1"/></svg>
  <svg style="left:573px" width="20" height="40" viewBox="0 0 20 40"><polyline points="2,2 18,20 2,38" fill="none" stroke="#fff" stroke-width="1"/></svg>
</section>

<div class="abs searchband">
  <label class="abs radio" style="left:43px"><i></i>All</label>
  <label class="abs radio" style="left:82px"><i></i>Song</label>
  <label class="abs radio" style="left:135px"><i></i>Artist</label>
  <div class="abs search-input">All Songs
    <svg class="abs" style="left:7px;top:8px" width="8" height="8" viewBox="0 0 8 8"><circle cx="3.2" cy="3.2" r="2.4" fill="none" stroke="#333" stroke-width="1.2"/><line x1="5" y1="5" x2="7.5" y2="7.5" stroke="#333" stroke-width="1.3"/></svg>
  </div>
  <div class="abs search-btn">Search</div>
</div>

<h2 class="abs results-title">MP3 FILES SEACH RESULTS</h2>

<article class="abs card" style="top:470px">
  <div class="top"></div>
  <div class="play"><svg width="11" height="14" viewBox="0 0 11 14"><polygon points="0,0 11,7 0,14" fill="#fff"/></svg></div>
  <div class="title">Download song: Marco Velleri Serpentina (Luis KKK Anders Dr</div>
  <div class="artist">Artist: Marco Velleri<span class="stars">&#9733;&#9733;&#9733;&#9734;&#9734;</span></div>
  <div class="wave"></div>
  <div class="meta"><span><b>Genre:</b> Minimal</span><span><b>Year:</b> 2011</span><span><b>Duration:</b> 00:07:35</span><span><b>Bitrate:</b> 320</span><span>Frequency: 44</span><span><b>Domain:</b> www.solennemusic.com</span></div>
  <div class="dl">DOWNLOAD<i></i></div>
</article>

<article class="abs card" style="top:614px">
  <div class="top"></div>
  <div class="play"><svg width="11" height="14" viewBox="0 0 11 14"><polygon points="0,0 11,7 0,14" fill="#fff"/></svg></div>
  <div class="title">Download song: Marco Velleri Serpentina (Luis KKK Anders Dr</div>
  <div class="artist">Artist: Marco Velleri<span class="stars">&#9733;&#9733;&#9733;&#9734;&#9734;</span></div>
  <div class="wave"></div>
  <div class="meta"><span><b>Genre:</b> Minimal</span><span><b>Year:</b> 2011</span><span><b>Duration:</b> 00:07:35</span><span><b>Bitrate:</b> 320</span><span>Frequency: 44</span><span><b>Domain:</b> www.solennemusic.com</span></div>
  <div class="dl">DOWNLOAD<i></i></div>
</article>

<article class="abs card" style="top:758px">
  <div class="top"></div>
  <div class="play"><svg width="11" height="14" viewBox="0 0 11 14"><polygon points="0,0 11,7 0,14" fill="#fff"/></svg></div>
  <div class="title">Download song: Marco Velleri Serpentina (Luis KKK Anders Dr</div>
  <div class="artist">Artist: Marco Velleri<span class="stars">&#9733;&#9733;&#9733;&#9734;&#9734;</span></div>
  <div class="wave"></div>
  <div class="meta"><span><b>Genre:</b> Minimal</span><span><b>Year:</b> 2011</span><span><b>Duration:</b> 00:07:35</span><span><b>Bitrate:</b> 320</span><span>Frequency: 44</span><span><b>Domain:</b> www.solennemusic.com</span></div>
  <div class="dl">DOWNLOAD<i></i></div>
</article>

<article class="abs card" style="top:902px">
  <div class="top"></div>
  <div class="play"><svg width="11" height="14" viewBox="0 0 11 14"><polygon points="0,0 11,7 0,14" fill="#fff"/></svg></div>
  <div class="title">Download song: Marco Velleri Serpentina (Luis KKK Anders Dr</div>
  <div class="artist">Artist: Marco Velleri<span class="stars">&#9733;&#9733;&#9733;&#9734;&#9734;</span></div>
  <div class="wave"></div>
  <div class="meta"><span><b>Genre:</b> Minimal</span><span><b>Year:</b> 2011</span><span><b>Duration:</b> 00:07:35</span><span><b>Bitrate:</b> 320</span><span>Frequency: 44</span><span><b>Domain:</b> www.solennemusic.com</span></div>
  <div class="dl">DOWNLOAD<i></i></div>
</article>

<nav>
  <span class="abs pager" style="left:178px;width:32px">Prev</span>
  <span class="abs pager" style="left:215px;width:16px">1</span>
  <span class="abs pager" style="left:236px;width:16px">2</span>
  <span class="abs pager" style="left:257px;width:16px">3</span>
  <span class="abs pager" style="left:279px;width:16px">4</span>
  <span class="abs pager" style="left:300px;width:16px">5</span>
  <span class="abs pager" style="left:321px;width:16px">6</span>
  <span class="abs pager" style="left:343px;width:16px">...</span>
  <span class="abs pager" style="left:364px;width:16px">22</span>
  <span class="abs pager" style="left:386px;width:32px">Next</span>
</nav>

<aside>
  <div class="abs ad" role="img" aria-label="Advertisement photo of a young man wearing headphones">
    <span class="label">ECHOWELL</span>
    <span class="head">Share the<br>headlines</span>
    <span class="btn"></span>
  </div>

  <div class="abs albums-head">
    <svg width="12" height="11" viewBox="0 0 12 11"><path d="M1.5 8 V6 a4.5 4.5 0 0 1 9 0 V8" fill="none" stroke="#fff" stroke-width="1.4"/><rect x="0.5" y="6.5" width="2.5" height="4" fill="#fff"/><rect x="9" y="6.5" width="2.5" height="4" fill="#fff"/></svg>
    LATEST ALBUMS
  </div>
  <div class="abs albums">
    <span class="ctrl" style="left:10px"></span>
    <span class="ctrl" style="left:27px"></span>
    <span class="ctrl" style="left:44px"></span>
    <span class="bar"></span>
    <ul>
      <li>Sed ut perspiciatis unde omnis</li>
      <li>Nemo enim ipsam volupta</li>
      <li>vel illum qui dolorem eum</li>
      <li>Quis autem vel eum iure repre</li>
      <li>Lorem ipsum dolor sit amet</li>
      <li>Ut enim ad minim veniam</li>
    </ul>
  </div>

  <div class="abs promo" role="img" aria-label="Promotional artwork with an orange music note button and a vintage microphone on a wooden table"></div>
</aside>

<svg class="abs shadow" viewBox="0 0 445 28" aria-hidden="true">
  <defs><radialGradient id="sh" cx="50%" cy="0%" r="60%"><stop offset="0" stop-color="#000" stop-opacity=".85"/><stop offset="1" stop-color="#000" stop-opacity="0"/></radialGradient></defs>
  <path d="M0 0 H445 Q222 40 0 0 Z" fill="url(#sh)"/>
</svg>

<footer>
  <span class="abs fsoc" style="left:310px;background:#3b5998"></span>
  <span class="abs fsoc" style="left:331px;background:#e8161c"></span>
  <span class="abs fsoc" style="left:353px;background:#f6a01a"></span>
  <span class="abs fsoc" style="left:374px;background:#33aae0"></span>
  <span class="abs fsoc" style="left:395px;background:#27c2c8"></span>
  <span class="abs fsoc" style="left:417px;background:#e62117"></span>
  <div class="abs flinks">HOME &nbsp;/ &nbsp;ABOUT US / &nbsp;OUR SERVICES &nbsp;/ &nbsp;REVIEWS &nbsp;/ &nbsp;CONTACT US</div>
  <div class="abs copy">2016 &copy; Copyrights Solenne Music.All Rights Reserved</div>
</footer>

</body>
</html>
```